Casino with the 'highest winning percentage' needs a stationery design

This is for a casino in Colombo, Sri Lanka and we need a stationery design for business card, letter head and envelope.

Should be very professional, simple and elegant without fancy fonts

Reason: Not fully satisfied with the designs. Need more designs.

Business

• 1. card deck symbol 'CLUBS' in red, or black

2. name in BLOCK CAPITAL LETTERS

3. Preferred font colours are black, white or red

4. Prefer 'professional /elegant' fonts
• SHOULD NOT HAVE ANY OTHER SYMBOL EXCEPT 'CLUBS'

DO NOT PREFER ITALIC FONTS

```html
<!DOCTYPE html>
<html lang="en">
<head>
<meta charset="utf-8">
<title>Crestmoor Entertainment – Business Card</title>
<link rel="stylesheet" href="https://fonts.googleapis.com/css2?family=PT+Serif:wght@400;700&display=swap">
<style>
  :root {
    --stage: #ebe8e4;
    --card: #ffffff;
    --red: #e30d31;
    --red-faint: #fbe9ec;
    --ink: #141414;
    --text: #222222;
    --card-edge: #8a8a8a;
  }
  * { box-sizing: border-box; margin: 0; padding: 0; }
  html, body { width: 1200px; height: 372px; overflow: hidden; }
  body {
    background: var(--stage);
    font-family: "PT Serif", Georgia, serif;
    color: var(--text);
    position: relative;
  }
  .card {
    position: absolute;
    top: 24px;
    width: 555px;
    height: 316px;
    background: var(--card);
    border: 1px solid var(--card-edge);
    overflow: hidden;
  }
  .card--front { left: 27px; }
  .card--back { left: 609px; }

  .side-band {
    position: absolute; left: 0; top: 0;
    width: 71px; height: 100%;
    background: var(--red);
  }
  .side-rule {
    position: absolute; left: 75px; top: 0;
    width: 3px; height: 100%;
    background: var(--ink);
  }
  .mark-dot { position: absolute; }
  .mark-dot--front { left: 21px; top: 14px; }
  .mark-dot--faint { left: 432px; top: 222px; }
  .mark-dot--back { left: 64px; top: 97px; }

  .brand-name {
    position: absolute;
    font-weight: 700;
    color: var(--ink);
    letter-spacing: 0.02em;
    line-height: 1.2;
  }
  .card--front .brand-name { left: 138px; top: 28px; font-size: 29px; }
  .card--back .brand-name { left: 194px; top: 106px; font-size: 34px; }

  .contact { position: absolute; left: 86px; font-size: 14px; line-height: 20.5px; }
  .contact__company { color: var(--red); font-weight: 700; font-size: 13.5px; }
  .contact--address { top: 129px; }
  .contact--lines { top: 203px; }
  .contact__key { color: var(--red); font-weight: 700; }
  .contact__web-name { color: var(--red); font-weight: 700; }

  .tagline {
    position: absolute; left: 0; right: 0; top: 261px;
    text-align: center;
    color: var(--red);
    font-weight: 700;
    font-size: 14.5px;
    letter-spacing: 0.14em;
  }
</style>
</head>
<body>
  <section class="card card--front">
    <div class="side-band"></div>
    <div class="side-rule"></div>
    <svg class="mark-dot mark-dot--faint" width="96" height="96" aria-hidden="true">
      <circle cx="48" cy="48" r="46" fill="var(--red-faint)"/>
    </svg>
    <svg class="mark-dot mark-dot--front" width="94" height="94" aria-hidden="true">
      <circle cx="47" cy="47" r="42" fill="var(--red)" stroke="#ffffff" stroke-width="5"/>
    </svg>
    <h1 class="brand-name">CRESTMOOR<br>ENTERTAINMENT</h1>
    <div class="contact contact--address">
      <p class="contact__company">CRESTMOOR LIMITED</p>
      <p>18, Lotus Garden Road</p>
      <p>Colombo 01000, Sri Lanka</p>
    </div>
    <div class="contact contact--lines">
      <p><span class="contact__key">P :</span> + 94 11 2450318</p>
      <p><span class="contact__key">C :</span> + 94 77 1234567</p>
      <p><span class="contact__key">F :</span> + 94 11 2450319</p>
      <p><span class="contact__key">E :</span> info@crestmoorcolombo.com</p>
      <p>www.<span class="contact__web-name">crestmoorcolombo</span>.com</p>
    </div>
  </section>

  <section class="card card--back">
    <svg class="mark-dot mark-dot--back" width="104" height="104" aria-hidden="true">
      <circle cx="52" cy="52" r="50" fill="var(--red)"/>
    </svg>
    <h2 class="brand-name">CRESTMOOR<br>ENTERTAINMENT</h2>
    <p class="tagline">HIGHEST WINNING PERCENTAGE IN THE WORLD</p>
  </section>
</body>
</html>
```